MRT Property - Business Cards

Looking for a business card & general letterhead, signage etc design for our new logo.

Colours:
000a20
0056a2
00b5ef
0088ce
68cef2

Fonts:
Poppins
Karla

Please keep look and feel of new brand - example in the zip package I sent.

```html
<!DOCTYPE html>
<html lang="en">
<head>
<meta charset="UTF-8">
<title>MRT Property – Letterhead</title>
<link href="https://fonts.googleapis.com/css2?family=Poppins:wght@400;700&display=swap" rel="stylesheet">
<style>
  :root {
    --navy: #000a20;
    --brand-blue: #0056a2;
    --mid-blue: #0088ce;
    --sky-blue: #00b5ef;
    --light-blue: #68cef2;
    --backdrop: #ececee;
    --paper: #ffffff;
    --ink: #1a1a1a;
  }
  * { margin: 0; padding: 0; box-sizing: border-box; }
  html, body {
    width: 1200px;
    height: 792px;
    overflow: hidden;
    background: var(--backdrop);
    font-family: "Poppins", sans-serif;
  }
  .letterhead {
    position: absolute;
    left: 338px;
    top: 26px;
    width: 524px;
    height: 740px;
    background: var(--paper);
    box-shadow: 0 2px 10px rgba(0, 10, 32, 0.12);
    overflow: hidden;
  }
  .brand {
    position: absolute;
    left: 80px;
    top: 38px;
    display: flex;
    align-items: center;
    gap: 8px;
  }
  .brand-dot {
    width: 18px;
    height: 18px;
    border-radius: 50%;
    background: var(--mid-blue);
  }
  .brand-name {
    font-weight: 700;
    font-size: 22px;
    letter-spacing: 0.2px;
    color: var(--brand-blue);
    line-height: 1;
  }
  .contact {
    position: absolute;
    right: 28px;
    top: 20px;
    text-align: right;
    color: var(--ink);
    font-size: 10.6px;
    line-height: 14px;
  }
  .contact-line {
    display: flex;
    justify-content: flex-end;
    align-items: center;
    gap: 6px;
    white-space: nowrap;
  }
  .contact-line svg { width: 9px; height: 9px; flex: none; }
  .address {
    margin-top: 14px;
    display: flex;
    justify-content: flex-end;
    align-items: flex-start;
    gap: 6px;
  }
  .address svg { width: 9px; height: 13px; flex: none; margin-top: 1px; }
  .footer-bands {
    position: absolute;
    left: 0;
    bottom: 0;
    width: 524px;
    height: 18px;
    display: block;
  }
</style>
</head>
<body>
  <main class="letterhead">
    <header>
      <div class="brand">
        <span class="brand-dot"></span>
        <span class="brand-name">MRT Property</span>
      </div>

      <address class="contact" style="font-style:normal">
        <div class="contact-line">+61 2 5550 1842
          <svg viewBox="0 0 10 10"><path d="M2.2 0.8 L3.6 2.8 L2.7 3.8 Q3.8 6.1 6.2 7.3 L7.2 6.4 L9.2 7.8 L8.3 9.3 Q4.5 9 2.1 6.2 Q0.6 4.2 0.8 1.7 Z" fill="var(--mid-blue)"/></svg>
        </div>
        <div class="contact-line">www.mrtproperty.com.au
          <svg viewBox="0 0 10 10"><circle cx="5" cy="5" r="4.3" fill="none" stroke="var(--mid-blue)" stroke-width="1.1"/><ellipse cx="5" cy="5" rx="1.8" ry="4.3" fill="none" stroke="var(--mid-blue)" stroke-width="0.9"/><line x1="0.7" y1="5" x2="9.3" y2="5" stroke="var(--mid-blue)" stroke-width="0.9"/></svg>
        </div>
        <div class="contact-line">hello@mrtproperty.com.au
          <svg viewBox="0 0 10 10"><rect x="0.6" y="2" width="8.8" height="6.2" rx="0.6" fill="none" stroke="var(--mid-blue)" stroke-width="1"/><path d="M0.8 2.4 L5 5.6 L9.2 2.4" fill="none" stroke="var(--mid-blue)" stroke-width="1"/></svg>
        </div>
        <div class="address">
          <div>Suite 4.12, Level 4<br>18 Harbourline Road, Rhodes,<br>Waterside NSW 2138</div>
          <svg viewBox="0 0 10 14"><path d="M5 0.7 A4 4 0 0 1 9 4.7 C9 7.5 5 11 5 11 C5 11 1 7.5 1 4.7 A4 4 0 0 1 5 0.7 Z" fill="none" stroke="var(--mid-blue)" stroke-width="1.1"/><circle cx="5" cy="4.7" r="1.5" fill="var(--mid-blue)"/><ellipse cx="5" cy="12.6" rx="3" ry="0.8" fill="none" stroke="var(--mid-blue)" stroke-width="0.8"/></svg>
        </div>
      </address>
    </header>

    <svg class="footer-bands" viewBox="0 0 876 30" preserveAspectRatio="none" aria-hidden="true">
      <polygon class="band-light" points="0,0 437,0 424,13 0,13" fill="var(--light-blue)"/>
      <polygon class="band-dark" points="450,0 876,0 876,30 187,30 200,19 432,19" fill="var(--mid-blue)"/>
    </svg>
  </main>
</body>
</html>
```